Redesign of business card for Cedar Ridge Mechanical

We are looking for a new design for our business cards for Cedar Ridge Mechanical. We are a plumbing & HVAC construction company, operating on the West Coast of Canada and USA. Logo attached.
Industry/Entity Type
Construction - Plumbing & HVAC
Contact Information for Business Card
Name, address, phone numbers, email, website address
Look and feel
Each slider illustrates characteristics of the customer's brand and the style your logo design should communicate.

```html
<!DOCTYPE html>
<html lang="en">
<head>
<meta charset="utf-8">
<title>Cedar Ridge Mechanical – Business Card</title>
<link href="https://fonts.googleapis.com/css2?family=Oswald:wght@500;700&family=Arimo:wght@400&display=swap" rel="stylesheet">
<style>
  :root {
    --stage: #2b2b2d;
    --card: #4a5264;
    --card-deep: #3d4454;
    --ink: #ffffff;
    --ink-soft: #e6e9ef;
    --pattern-light: #c9d1e0;
    --pattern-dark: #232733;
  }
  * { margin: 0; padding: 0; box-sizing: border-box; }
  html, body { width: 1200px; height: 875px; overflow: hidden; }
  body {
    background: var(--stage);
    display: flex;
    align-items: center;
    justify-content: center;
    gap: 28px;
    font-family: "Arimo", Arial, sans-serif;
  }
  .card {
    position: relative;
    width: 560px;
    height: 320px;
    border-radius: 18px;
    background: var(--card);
    overflow: hidden;
  }
  /* Back face */
  .card-back .pattern-field {
    position: absolute;
    inset: 0;
    background: linear-gradient(135deg, var(--pattern-light) 0%, var(--card) 45%, var(--pattern-dark) 100%);
    opacity: 0.55;
  }
  .card-back .back-mark {
    position: absolute;
    left: 338px;
    top: 142px;
    display: flex;
    align-items: center;
    gap: 8px;
    color: var(--ink);
    font-family: "Oswald", sans-serif;
    font-weight: 500;
    font-size: 15px;
    letter-spacing: 0.04em;
    text-transform: uppercase;
  }
  .back-mark .mark-square {
    width: 12px; height: 12px; background: var(--ink);
  }
  /* Front face */
  .edge-bar {
    position: absolute;
    width: 18px;
    height: 120px;
    background: var(--ink);
    border-radius: 9px;
  }
  .edge-bar.left { left: -6px; bottom: 22px; }
  .edge-bar.right { right: -6px; top: 22px; }
  .front-brand {
    position: absolute;
    left: 40px;
    top: 0;
    width: 230px;
    height: 100%;
    display: flex;
    align-items: center;
    justify-content: center;
    gap: 10px;
    color: var(--ink);
    font-family: "Oswald", sans-serif;
    font-weight: 500;
    font-size: 22px;
    line-height: 1.15;
    letter-spacing: 0.03em;
    text-transform: uppercase;
  }
  .front-brand .mark-square { flex: none; width: 20px; height: 20px; background: var(--ink); }
  .divider {
    position: absolute;
    left: 292px;
    top: 68px;
    width: 1px;
    height: 184px;
    background: var(--ink-soft);
  }
  .contact {
    position: absolute;
    left: 314px;
    top: 64px;
    color: var(--ink-soft);
  }
  .contact .person-name {
    font-family: "Oswald", sans-serif;
    font-weight: 700;
    font-size: 26px;
    letter-spacing: 0.06em;
    color: var(--ink);
    line-height: 1;
  }
  .contact .person-title {
    font-size: 13px;
    margin: 4px 0 14px;
  }
  .contact ul { list-style: none; }
  .contact li {
    display: flex;
    align-items: flex-start;
    gap: 8px;
    font-size: 11.5px;
    line-height: 1.35;
    margin-bottom: 4px;
  }
  .contact svg { flex: none; width: 10px; height: 10px; margin-top: 3px; fill: var(--ink-soft); }
</style>
</head>
<body>
  <section class="card card-back" aria-label="Card back">
    <div class="pattern-field" role="img" aria-label="Repeating brand-mark pattern in metallic foil and gloss on slate"></div>
    <div class="back-mark"><span class="mark-square"></span>Cedar Ridge Mechanical</div>
  </section>

  <section class="card card-front" aria-label="Card front">
    <span class="edge-bar left"></span>
    <span class="edge-bar right"></span>
    <div class="front-brand"><span class="mark-square"></span><span>Cedar Ridge<br>Mechanical</span></div>
    <span class="divider"></span>
    <div class="contact">
      <p class="person-name">DANIEL HART</p>
      <p class="person-title">Founder &amp; CEO</p>
      <ul>
        <li><svg viewBox="0 0 10 10"><path d="M5 0a3.5 3.5 0 0 0-3.5 3.5C1.5 6 5 10 5 10s3.5-4 3.5-6.5A3.5 3.5 0 0 0 5 0zm0 5a1.4 1.4 0 1 1 0-2.8A1.4 1.4 0 0 1 5 5z"/></svg><span>423 Street Address Here, City<br>State &amp; Country, ZIP Code</span></li>
        <li><svg viewBox="0 0 10 10"><path d="M2 0l2 2.5-1 1.2a6 6 0 0 0 3.3 3.3l1.2-1L10 8l-1.5 2C4 10 0 6 0 1.5z"/></svg><span>1-123-456-7890</span></li>
        <li><svg viewBox="0 0 10 10"><path d="M2 0l2 2.5-1 1.2a6 6 0 0 0 3.3 3.3l1.2-1L10 8l-1.5 2C4 10 0 6 0 1.5z"/></svg><span>123-456-7890</span></li>
        <li><svg viewBox="0 0 10 10"><path d="M2.5 0h5a1 1 0 0 1 1 1v8a1 1 0 0 1-1 1h-5a1 1 0 0 1-1-1V1a1 1 0 0 1 1-1zm.5 1.5v6h4v-6z"/></svg><span>123-456-7890</span></li>
        <li><svg viewBox="0 0 10 10"><path d="M0 2h10v6H0zm1 1v.3l4 2.5 4-2.5V3z"/></svg><span>info@yourwebsitehere.com</span></li>
        <li><svg viewBox="0 0 10 10"><circle cx="5" cy="5" r="4.5"/></svg><span>yourwebsitehere.com</span></li>
      </ul>
    </div>
  </section>
</body>
</html>
```